Lotstallmart.com Webpage Design

Design Brief for lotstallmart.com (Copy of Brief also in attached Word file)

Name of Website- lotstallmart.com (existing logo and look & feel of website to be changed)

Logo - Finalised. The logo files are attached with the brief as “logo.jpeg”. The “Blue- Grey” version of the logo is for use on lighter backgrounds and the “Orange-White” version of the logo is for use on darker backgrounds. (A full Black version of the logo is also attached). Both versions may be used in different parts of the website. All attached files are in .png format.
Status - The website in functional and is undergoing user trials. However, we want to improve the look & feel of the website so at it seems
a. cotemporary,
b. Easy to Navigate
c. professional and
d. Vibrant.

Please visit ‘lotstallmart.com’ to check out the website and its functionalities – please use it only as a reference for the features & functions to be provided, however the designer should use a ‘Free Hand’ in designing the composition of various parts of the webpage without getting too influenced by the existing design

Objective of the Website ‘lotstallmart.com –
a. It is a portal focussed on listing of ‘Retail’ specific real-estate properties by developers, owners and realty brokers. The properties shall listed under the following four categories-
i. Retail Malls
ii. Shopping Complexes
iii. High-street shops
iv. Retail Warehouses
*refer lotstallmart.com for better clarity

b. The abovementioned properties shall be listed either for ‘Sale’ or ‘rent\lease’ or both

c. Users shall visit the site in case they wish to acquire a retail \ shop space either on ‘sale’ or ‘rent’. These Users would be able to specify the ‘Search Criteria’ through the tool-bars provided on the website – the ‘Search Criteria’ shall comprise of ‘Type of space category’, ‘City’, ‘Locality’, transaction type ie ‘Rent \ Sale’ and ‘Area Range’

d. The main revenue model for the website shall be listing fee ( or advertising charges ) payable by those listing their properties on the website.

Three Main Pages of Website (lotstallmart.com) that need to be designed -
a. Main Home Page (visit the web link - http://lotstallmart.com/ ) - The main home page has the “Search Toolbar” for specifying of Search Criteria by the User. It shall also have the following features & functions-
i. Main Advertising Banner
ii. Featured Projects
iii. New Launches
iv. Toolbar with buttons – ‘Advertise with Us’, ‘Listings Alert’, ‘Mart Wizards’, ‘Advertiser Login’

b. Property Listings Page (visit the web link - http://lotstallmart.com/gurgaon-in-india ) - The List of property options that match the Criteria specified by the ‘User’ get displayed on this page.

c. Property Detail Page - When the ‘User’ clicks on the “More….” Button on the ‘Property Listings Page’ (given in point b. above) the web page with the details of the property opens. (For Example – visit the web link - http://lotstallmart.com/vorne-Shopping-Complex-vorne-quadrion-gurgaon-636 )

Note:- Please refer to attached ‘Shopping’ related images the designer may use them on the website to provide a look & feel of retail if required – either separately or rotate in a single window

Target Market(s)

Retailers & Investors looking for retail space, Real Estate Brokers, Developers

Industry/Entity Type

Advertising

Number of Pages Required

3 page

Requirements
Must have
• Refer to existing site lotstallmart.com -- all the existing functionalities are a must have.
Nice to have
• The Designer may use the retail related images on the website if required for making it more vibrant. Refer attached images Shopping(1-6).jpg

```html
<!DOCTYPE html>
<html lang="en">
<head>
<meta charset="utf-8">
<title>Lotstallmart.com – Retail Space Portal</title>
<link href="https://fonts.googleapis.com/css2?family=Open+Sans:wght@400;600;700&display=swap" rel="stylesheet">
<style>
:root{
  --blue:#2196f3;
  --blue-light:#4db2ff;
  --blue-dark:#1a7fe0;
  --yellow:#fbbf16;
  --yellow-dark:#f5a500;
  --red:#d8161b;
  --ink:#222;
  --muted:#555;
  --footer:#e1e1e1;
  --footer-ink:#555;
  --bottom:#222;
  --white:#fff;
}
*{box-sizing:border-box;margin:0;padding:0}
html,body{width:1200px;height:2486px;overflow:hidden;background:var(--white)}
body{font-family:"Open Sans",Arial,sans-serif;color:var(--ink);position:relative}
.abs{position:absolute}

/* top strip */
.topbar{left:0;top:0;width:1200px;height:42px;background:linear-gradient(var(--blue-light),var(--blue))}
.topbar .cities{left:60px;top:11px;font-size:13px;color:var(--white)}
.topbar .social{right:64px;top:13px;display:flex;gap:6px}
.topbar .social span{width:15px;height:15px;background:var(--white);border-radius:2px;display:block}

/* header */
.header{left:0;top:42px;width:1200px;height:122px;background:var(--white)}
.logo{left:60px;top:38px;display:flex;align-items:center;gap:10px}
.logo .dot{width:34px;height:34px;border-radius:50%;background:var(--blue)}
.logo .name{font-size:34px;font-weight:700;color:var(--blue);letter-spacing:-.5px}
.nav-item{top:46px;font-size:15px;color:#555;text-align:center;transform:translateX(-50%);white-space:nowrap}
.nav-item svg{display:block;margin:0 auto 6px}
.nav-item.active{color:var(--blue)}
.btn-login{left:1007px;top:52px;width:133px;height:40px;background:var(--blue);color:var(--white);font-size:15px;border-radius:3px;display:flex;align-items:center;justify-content:center}

/* hero */
.hero{left:0;top:164px;width:1200px;height:471px;background:radial-gradient(ellipse at 62% 40%,#d8b9a0 0%,#a6724e 35%,#5a3a2a 70%,#2d2320 100%)}
.hero-title{left:61px;top:150px;font-size:36px;line-height:46px;color:var(--white);font-weight:400}
.btn-hero{left:60px;top:268px;width:172px;height:60px;background:linear-gradient(var(--blue-light),var(--blue));color:var(--white);font-size:15px;border-radius:3px;display:flex;align-items:center;justify-content:center}
.dots{left:578px;top:380px;display:flex;gap:13px}
.dots span{width:8px;height:8px;border-radius:50%;background:var(--white)}
.dots span.on{background:var(--blue)}

/* search */
.search{left:60px;top:582px;width:1080px;height:106px;background:linear-gradient(var(--blue-light),var(--blue));border-radius:3px;box-shadow:0 26px 22px -18px rgba(0,0,0,.35)}
.field{top:31px;height:43px;background:var(--white);font-size:15px;color:#555;padding-left:16px;display:flex;align-items:center;justify-content:space-between;padding-right:14px}
.btn-search{left:944px;top:31px;width:114px;height:43px;background:var(--yellow);color:var(--ink);font-size:15px;display:flex;align-items:center;justify-content:center}

/* categories */
.cat{top:750px;width:260px;text-align:center;transform:translateX(-50%)}
.cat .ico{width:120px;height:120px;border-radius:50%;background:linear-gradient(var(--blue-light),var(--blue-dark));margin:0 auto;display:flex;align-items:center;justify-content:center}
.cat h3{font-size:22px;font-weight:400;margin-top:24px;color:var(--ink);white-space:nowrap}
.cat p{font-size:13px;line-height:17px;color:var(--muted);margin-top:12px;padding:0 16px}

/* listings */
.section-title{left:58px;font-size:26px;font-weight:400;color:var(--ink)}
.arrows{left:1106px;display:flex;gap:12px}
.card{width:260px;overflow:hidden}
.card .photo{width:260px;height:194px;position:relative}
.card .city{position:absolute;left:0;bottom:0;background:var(--red);color:var(--white);font-size:15px;padding:5px 10px}
.card h4{font-size:19px;letter-spacing:-.4px;font-weight:400;margin-top:24px;white-space:nowrap;color:var(--ink)}
.card h4 small{font-size:13px;letter-spacing:-.2px}
.card .type{font-size:13px;font-weight:600;margin-top:3px}
.card .btn-view{margin-top:14px;width:88px;height:30px;background:var(--blue);color:var(--white);font-size:12px;display:flex;align-items:center;justify-content:center;border-radius:2px}

/* alert band */
.alert{left:0;top:1455px;width:1200px;height:137px;background:linear-gradient(var(--blue-light),var(--blue))}
.alert h2{position:absolute;left:58px;top:33px;font-size:27px;font-weight:400;color:var(--white)}
.alert p{position:absolute;left:58px;top:76px;font-size:13px;color:var(--white)}
.alert .input{position:absolute;left:543px;top:40px;width:400px;height:61px;background:var(--white);font-size:15px;color:#888;padding-left:16px;display:flex;align-items:center}
.alert .btn-sub{position:absolute;left:971px;top:40px;width:169px;height:61px;background:var(--yellow);font-size:23px;display:flex;align-items:center;justify-content:center;color:var(--ink)}

/* footer */
.footer{left:0;top:2041px;width:1200px;height:365px;background:var(--footer)}
.footer h5{position:absolute;top:38px;font-size:26px;font-weight:400;color:#444}
.about-text{position:absolute;left:61px;top:98px;width:300px;font-size:12.5px;line-height:22px;color:var(--footer-ink)}
.circles{position:absolute;left:62px;top:222px;display:flex;gap:3px}
.circles span{width:32px;height:32px;border-radius:50%;background:#999;display:block}
.links{position:absolute;top:96px;list-style:none;font-size:12.5px;line-height:22px;color:var(--footer-ink)}
.links li::before{content:"";display:inline-block;border-left:5px solid #555;border-top:4px solid transparent;border-bottom:4px solid transparent;margin-right:10px}
.f-input{position:absolute;left:799px;width:341px;background:var(--white);font-size:14px;color:#888;padding:16px 18px}
.btn-send{position:absolute;left:797px;top:289px;width:86px;height:40px;background:var(--blue);color:var(--white);font-size:14px;display:flex;align-items:center;justify-content:center;border-radius:2px}
.bottom{left:0;top:2406px;width:1200px;height:80px;background:var(--bottom);color:#aaa;font-size:13px;display:flex;align-items:center;justify-content:center}
</style>
</head>
<body>

<div class="abs topbar">
  <div class="abs cities">Bangalore | Chennai | Greater Noida | Gurgaon | Hyderabad | Jaipur | Khanna | Kolkatta | Mumbai | Noida | Pune | Surat</div>
  <div class="abs social"><span></span><span></span><span></span><span></span></div>
</div>

<header class="abs header">
  <div class="abs logo"><span class="dot"></span><span class="name">lotstallmart.com</span></div>
  <div class="abs nav-item active" style="left:480px">
    <svg width="16" height="14" viewBox="0 0 16 14"><path d="M8 0 L16 7 H13 V14 H9.5 V9 H6.5 V14 H3 V7 H0 Z" fill="currentColor"/></svg>Home</div>
  <div class="abs nav-item" style="left:621px">
    <svg width="16" height="14" viewBox="0 0 16 14"><path d="M16 0 L0 6 L5 8 L6 14 L9 9 L13 12 Z" fill="currentColor"/></svg>Advertise with us</div>
  <div class="abs nav-item" style="left:784px">
    <svg width="16" height="14" viewBox="0 0 16 14"><path d="M0 0 H3 L4 2 H16 L14 8 H5 L5.5 9.5 H14 V11 H4.5 L2 1.5 H0 Z" fill="currentColor"/><circle cx="6" cy="12.8" r="1.2" fill="currentColor"/><circle cx="13" cy="12.8" r="1.2" fill="currentColor"/></svg>Mart Wizards</div>
  <div class="abs nav-item" style="left:926px">
    <svg width="16" height="14" viewBox="0 0 16 14"><path d="M8 0 C4 0 3.5 3 3.5 5 V8 L1.5 11 H14.5 L12.5 8 V5 C12.5 3 12 0 8 0 Z" fill="currentColor"/><circle cx="8" cy="12.5" r="1.5" fill="currentColor"/></svg>Listing Alert</div>
  <div class="abs btn-login">Advertiser Login</div>
</header>

<section class="abs hero" role="img" aria-label="Photo of a smiling couple shopping in a brightly lit mall">
  <h1 class="abs hero-title">Harbor Square<br>Chennai</h1>
  <div class="abs btn-hero">Advertise with Us</div>
  <div class="abs dots"><span></span><span class="on"></span><span></span></div>
</section>

<form class="abs search">
  <div class="abs field" style="left:20px;width:217px">Rent <svg width="9" height="6"><path d="M1 1 L4.5 4.5 L8 1" stroke="#555" fill="none" stroke-width="1.4"/></svg></div>
  <div class="abs field" style="left:250px;width:217px">City <svg width="9" height="6"><path d="M1 1 L4.5 4.5 L8 1" stroke="#555" fill="none" stroke-width="1.4"/></svg></div>
  <div class="abs field" style="left:480px;width:217px">Locality <svg width="9" height="6"><path d="M1 1 L4.5 4.5 L8 1" stroke="#555" fill="none" stroke-width="1.4"/></svg></div>
  <div class="abs field" style="left:712px;width:217px">Keywords <svg width="9" height="6"><path d="M1 1 L4.5 4.5 L8 1" stroke="#555" fill="none" stroke-width="1.4"/></svg></div>
  <div class="abs btn-search">Search</div>
</form>

<div class="abs cat" style="left:169px">
  <div class="ico"><svg width="60" height="60" viewBox="0 0 60 60" fill="#fff"><rect x="8" y="12" width="44" height="44"/><g fill="#2196f3"><rect x="14" y="18" width="7" height="7"/><rect x="26" y="18" width="7" height="7"/><rect x="38" y="18" width="7" height="7"/><rect x="14" y="30" width="7" height="7"/><rect x="26" y="30" width="7" height="7"/><rect x="38" y="30" width="7" height="7"/><rect x="25" y="43" width="10" height="13"/></g></svg></div>
  <h3>Retail Malls</h3>
  <p>Sed ut perspiciatis unde omnis iste natus error sit voluptatem accusan-tium doloremque</p>
</div>
<div class="abs cat" style="left:451px">
  <div class="ico"><svg width="60" height="60" viewBox="0 0 60 60"><path d="M14 20 H46 L50 54 H10 Z" fill="#fff"/><path d="M22 24 V16 A8 8 0 0 1 38 16 V24" stroke="#fff" stroke-width="3" fill="none"/></svg></div>
  <h3>Shopping Complex</h3>
  <p>Sed ut perspiciatis unde omnis iste natus error sit voluptatem accusan-tium doloremque</p>
</div>
<div class="abs cat" style="left:754px">
  <div class="ico"><svg width="64" height="60" viewBox="0 0 64 60" fill="#fff"><rect x="22" y="4" width="20" height="8" rx="1"/><path d="M6 16 H58 L60 26 H4 Z"/><rect x="8" y="28" width="48" height="26"/><rect x="14" y="33" width="16" height="12" fill="#2196f3"/><rect x="36" y="33" width="14" height="21" fill="#2196f3"/></svg></div>
  <h3>High Street Shops</h3>
  <p>Sed ut perspiciatis unde omnis iste natus error sit voluptatem accusan-tium doloremque</p>
</div>
<div class="abs cat" style="left:1032px">
  <div class="ico"><svg width="60" height="60" viewBox="0 0 60 60" fill="#fff"><path d="M10 8 L16 8 L24 48 H50" stroke="#fff" stroke-width="3" fill="none"/><circle cx="26" cy="52" r="4"/><circle cx="46" cy="52" r="4"/><rect x="24" y="30" width="14" height="14"/><rect x="38" y="22" width="12" height="22"/></svg></div>
  <h3>Retail Warehouses</h3>
  <p>Sed ut perspiciatis unde omnis iste natus error sit voluptatem accusan-tium doloremque</p>
</div>

<h2 class="abs section-title" style="top:1034px">Featured Projects</h2>
<div class="abs arrows" style="top:1043px">
  <svg width="12" height="18"><path d="M10 2 L3 9 L10 16" stroke="#222" stroke-width="2.4" fill="none"/></svg>
  <svg width="12" height="18"><path d="M2 2 L9 9 L2 16" stroke="#222" stroke-width="2.4" fill="none"/></svg>
</div>

<article class="abs card" style="left:60px;top:1100px">
  <div class="photo" role="img" aria-label="Photo of white residential towers" style="background:linear-gradient(#a9cdee,#e8ecef 45%,#c7ccd0)"><span class="city">Surat</span></div>
  <h4>Meridian Heights</h4><div class="type">Shopping Complex</div><div class="btn-view">View Details</div>
</article>
<article class="abs card" style="left:333px;top:1100px">
  <div class="photo" role="img" aria-label="Photo of an open-air shopping street with palm trees" style="background:linear-gradient(#c9a9a5,#b99a7c 45%,#6f6a5c)"><span class="city">Faridabad</span></div>
  <h4>Ora 81 High Street, <small>Sector-81</small></h4><div class="type">Shopping Complex</div><div class="btn-view">View Details</div>
</article>
<article class="abs card" style="left:608px;top:1100px">
  <div class="photo" role="img" aria-label="Aerial photo of glass towers beside a green park and lake" style="background:linear-gradient(#b8c8d8,#8fa59a 50%,#5f8c55)"><span class="city">Gurgaon</span></div>
  <h4>Kestrel Cosmopolis</h4><div class="type">Shopping Complex</div><div class="btn-view">View Details</div>
</article>
<article class="abs card" style="left:880px;top:1100px">
  <div class="photo" role="img" aria-label="Photo of a lit shopping mall at sunset" style="background:linear-gradient(#4f6fa8,#c99a80 50%,#6a4e4a)"><span class="city">New Delhi</span></div>
  <h4>Tidal Mall-Lotus Garden</h4><div class="type">Shopping Complex</div><div class="btn-view">View Details</div>
</article>

<section class="abs alert">
  <h2>Listing Alert</h2>
  <p>Suscribe&nbsp; for Fortnightly Email update on New Listings @ Lotstallmart</p>
  <div class="input">Enter your mail Addrtess</div>
  <div class="btn-sub">Subscribe</div>
</section>

<h2 class="abs section-title" style="top:1624px">Featured New Launches</h2>
<div class="abs arrows" style="top:1633px">
  <svg width="12" height="18"><path d="M10 2 L3 9 L10 16" stroke="#222" stroke-width="2.4" fill="none"/></svg>
  <svg width="12" height="18"><path d="M2 2 L9 9 L2 16" stroke="#222" stroke-width="2.4" fill="none"/></svg>
</div>

<article class="abs card" style="left:60px;top:1690px">
  <div class="photo" role="img" aria-label="Photo of a multi-storey mall facade" style="background:linear-gradient(#6f9ed8,#c8ccd4 50%,#3a4a6a)"><span class="city">Bhopal</span></div>
  <h4>The Grand Bazaar Place</h4><div class="type">Shopping Complex</div><div class="btn-view">View Details</div>
</article>
<article class="abs card" style="left:333px;top:1690px">
  <div class="photo" role="img" aria-label="Rendering of a curved modern office block among trees" style="background:linear-gradient(#8e9b78,#7d8576 50%,#4c5a3e)"><span class="city">Noida</span></div>
  <h4>Crest One</h4><div class="type">Shopping Complex</div><div class="btn-view">View Details</div>
</article>
<article class="abs card" style="left:608px;top:1690px">
  <div class="photo" role="img" aria-label="Rendering of a shopping plaza with storefront signs" style="background:linear-gradient(#44587c,#8a5a52 55%,#5b6a6e)"><span class="city">Mohali</span></div>
  <h4>Town Core</h4><div class="type">Shopping Complex</div><div class="btn-view">View Details</div>
</article>
<article class="abs card" style="left:880px;top:1690px">
  <div class="photo" role="img" aria-label="Rendering of tall residential towers at dusk" style="background:linear-gradient(#7c6c62,#b48b68 50%,#5a4a40)"><span class="city">Mohali</span></div>
  <h4>SCO In Sector</h4><div class="type">Shopping Complex</div><div class="btn-view">View Details</div>
</article>

<footer class="abs footer">
  <h5 style="left:61px">About us</h5>
  <p class="about-text">Lotstallmart.com - About Us<br>Lotstallmart.com is a Specialised Web based platform for Retail Space, featuring properties across India under various formats such as Retail Malls, Shopping Complexes,</p>
  <div class="circles"><span></span><span></span><span></span><span></span></div>

  <h5 style="left:421px">Quick Links</h5>
  <ul class="links" style="left:421px"><li>About Us</li><li>Privacy Policy</li><li>Terms of Use</li><li>Contact Us</li><li>Site Map</li></ul>
  <ul class="links" style="left:595px"><li>Retail Malls</li><li>Shopping Complex</li><li>High Street Shops</li><li>Retail Warehouses</li></ul>

  <h5 style="left:799px">Mart Wizards</h5>
  <div class="f-input" style="top:93px;height:55px">Enter your mail Addrtess</div>
  <div class="f-input" style="top:158px;height:116px">Enter your mail Addrtess</div>
  <div class="btn-send">Send</div>
</footer>

<div class="abs bottom">Copyright © 2015&nbsp; Lotstallmart.com. All rights reserved.</div>

</body>
</html>
```